Luxury Business Card Design for High-End Window Treatments

Gilded Slatworks
Custom Plantation Shutters & Architectural Shading Systems

⸻

BACK

Daniel Trevick
Owner

Custom Interior & Exterior Window Treatments

919-555-0148
gildedslatworks.com

I have included a picture that I’m hoping we can use on the back, but I’m also wondering if you can get rid of the ladder? Should we get rid of shutters , shades and blinds underneath Gilded Slatworks?

Target Market(s)

High-end residential homeowners, custom home builders, architects, interior designers, and luxury renovation clients seeking premium plantation shutters and motorized architectural shading systems.

Industry/Entity Type

Custom Window treatments

Contact Information for Business Card

Front Gilded Slatworks Custom Plantation Shutters Motorized Architectural Shading Systems BACK Daniel Trevick Owner 919-555-0148 GildedSlatworks.com Custom Interior & Exterior Window Treatments By Appointment

Requirements
Nice to have
• Not 100% sure on nice to halves or the color but you can definitely check out my website to get a better understanding of what I’m trying to do

```html
<!DOCTYPE html>
<html lang="en">
<head>
<meta charset="utf-8">
<title>Gilded Slatworks – Business Card</title>
<link rel="stylesheet" href="https://fonts.googleapis.com/css2?family=Libre+Baskerville:wght@400;700&family=Montserrat:wght@400;500&family=Zilla+Slab:wght@700&display=swap">
<style>
  :root {
    --stage: #d6d6d6;
    --card: #050505;
    --gold: #c9ae4e;
    --white: #f4f4f4;
    --photo-dark: #1d2430;
    --photo-mid: #4a5566;
    --photo-light: #9aa3ab;
  }
  * { margin: 0; padding: 0; box-sizing: border-box; }
  html, body { width: 1200px; height: 800px; overflow: hidden; }
  body {
    background: var(--stage);
    display: flex;
    align-items: center;
    justify-content: center;
    gap: 48px;
  }
  .card {
    position: relative;
    width: 540px;
    height: 310px;
    background: var(--card);
    border: 2px solid var(--gold);
    box-shadow: 0 10px 24px rgba(0,0,0,.25);
    overflow: hidden;
  }

  /* Back side */
  .card-back__photo-frame {
    position: absolute;
    left: 300px; top: 14px;
    width: 214px; height: 196px;
    background: var(--gold);
  }
  .card-back__photo {
    position: absolute;
    left: 286px; top: 0;
    width: 214px; height: 196px;
    background: linear-gradient(160deg, var(--photo-dark) 0%, var(--photo-mid) 45%, var(--photo-light) 75%, #3c4a32 100%);
  }
  .card-back__identity { position: absolute; left: 34px; top: 96px; }
  .card-back__name {
    font-family: "Zilla Slab", serif;
    font-weight: 700;
    font-size: 25px;
    color: var(--gold);
    line-height: 1;
  }
  .card-back__role {
    font-family: "Montserrat", sans-serif;
    font-size: 14px;
    color: var(--white);
    margin-top: 2px;
  }
  .card-back__contacts {
    position: absolute; left: 34px; top: 150px;
    list-style: none;
    font-family: "Montserrat", sans-serif;
    font-size: 12.5px;
    color: var(--white);
  }
  .card-back__contacts li { display: flex; align-items: center; gap: 8px; height: 18px; }
  .card-back__contacts svg { width: 12px; height: 12px; flex: none; }
  .card-back__tagline {
    position: absolute; left: 34px; top: 204px;
    width: 230px;
    font-family: "Libre Baskerville", serif;
    font-size: 12px;
    line-height: 17px;
    color: var(--gold);
  }

  /* Front side */
  .card-front__wordmark {
    position: absolute; right: 40px; top: 70px;
    font-family: "Libre Baskerville", serif;
    font-weight: 400;
    font-size: 42px;
    line-height: 1.1;
    color: var(--gold);
    text-align: right;
  }
  .card-front__services {
    position: absolute; left: 36px; bottom: 30px;
    list-style: none;
    font-family: "Libre Baskerville", serif;
    font-size: 13px;
    color: var(--white);
  }
  .card-front__services li { display: flex; align-items: center; gap: 8px; line-height: 20px; }
  .card-front__bullet {
    width: 9px; height: 9px;
    border: 1.5px solid var(--gold);
    border-radius: 50%;
    flex: none;
  }
</style>
</head>
<body>

  <section class="card card-back" aria-label="Card back">
    <div class="card-back__photo-frame"></div>
    <div class="card-back__photo" role="img" aria-label="Photo of a covered porch with white columns and dark exterior shades lowered between them"></div>

    <div class="card-back__identity">
      <p class="card-back__name">Daniel Trevick</p>
      <p class="card-back__role">Owner</p>
    </div>

    <ul class="card-back__contacts">
      <li>
        <svg viewBox="0 0 24 24" aria-hidden="true"><path fill="var(--gold)" d="M6.6 10.8a15 15 0 0 0 6.6 6.6l2.2-2.2c.3-.3.7-.4 1-.2 1.1.4 2.3.6 3.6.6.6 0 1 .4 1 1V20c0 .6-.4 1-1 1A17 17 0 0 1 3 4c0-.6.4-1 1-1h3.5c.6 0 1 .4 1 1 0 1.3.2 2.5.6 3.6.1.3 0 .7-.2 1z"/></svg>
        919-555-0148
      </li>
      <li>
        <svg viewBox="0 0 24 24" aria-hidden="true" fill="none" stroke="var(--gold)" stroke-width="2"><circle cx="12" cy="12" r="10"/><path d="M2 12h20M12 2c3 3 3 17 0 20M12 2c-3 3-3 17 0 20"/></svg>
        GildedSlatworks.com
      </li>
    </ul>

    <p class="card-back__tagline">Custom Interior &amp;<br>Exterior Window<br>Treatments<br>By Appointment</p>
  </section>

  <section class="card card-front" aria-label="Card front">
    <h1 class="card-front__wordmark">Gilded<br>Slatworks</h1>
    <ul class="card-front__services">
      <li><span class="card-front__bullet"></span>Gilded Slatworks Custom</li>
      <li><span class="card-front__bullet"></span>Plantation Shutters Motorized</li>
      <li><span class="card-front__bullet"></span>Architectural Shading Systems</li>
    </ul>
  </section>

</body>
</html>
```